Norvane Stationery Design Project

We need stationary design that goes with the attached logo. We have logo in two different versions. One in Red/Black and the other in Blue/Green. Red/Black is going to be our primary color and we are planning to use Blue/Green occasionally as necessary.

So we need stationary design in both color combinations. Maybe you can work with Red/Black first and once we decide on the design, then you can show the Blue/Green variation.

Please see the attached png and psd files for logo.

Target Market(s)

IT departments of Medium size Enterprises.

Industry/Entity Type

Work

Requirements
Must have
• -Letter head
-Cover page design for white papers and articles that are going to publish
-Business Card
-Envelope design
Nice to have
• - High level design template that we can follow for our internal web applications

```html
<!DOCTYPE html>
<html lang="en">
<head>
<meta charset="utf-8">
<title>Norvane Software – Business Card</title>
<link rel="stylesheet" href="https://fonts.googleapis.com/css2?family=Montserrat:wght@500;700;800&display=swap">
<style>
  :root {
    --backdrop: #2b2b2b;
    --card: #f7f7f7;
    --ink: #151515;
    --red: #d4111b;
    --black: #0c0c0c;
    --muted: #333333;
  }
  * { box-sizing: border-box; margin: 0; padding: 0; }
  html, body {
    width: 1200px;
    height: 997px;
    overflow: hidden;
    background: var(--backdrop);
    font-family: "Montserrat", Arial, sans-serif;
  }
  .card {
    position: absolute;
    left: 270px;
    width: 660px;
    height: 376px;
    background: linear-gradient(135deg, #ffffff 0%, var(--card) 60%, #ececec 100%);
    overflow: hidden;
    box-shadow: 0 18px 40px rgba(0,0,0,0.45);
  }
  .card--front { top: 90px; }
  .card--back  { top: 530px; }

  .card__band {
    position: absolute;
    left: 0;
    bottom: 0;
    width: 660px;
    height: 40px;
  }
  .band__red { fill: var(--red); }
  .band__black { fill: var(--black); }

  .wordmark {
    display: flex;
    align-items: center;
    gap: 14px;
    white-space: nowrap;
  }
  .wordmark__mark {
    width: 30px;
    height: 30px;
    flex: none;
    background: var(--red);
  }
  .wordmark__name {
    font-weight: 800;
    color: var(--ink);
    letter-spacing: 0.14em;
    text-transform: uppercase;
    line-height: 1;
  }
  .card--front .wordmark {
    position: absolute;
    left: 0;
    right: 0;
    top: 150px;
    justify-content: center;
  }
  .card--front .wordmark__name { font-size: 36px; }
  .card--front .wordmark__mark { width: 36px; height: 36px; }

  .card--back .wordmark {
    position: absolute;
    left: 36px;
    top: 170px;
    gap: 12px;
  }
  .card--back .wordmark__name {
    font-size: 18px;
    letter-spacing: 0.1em;
  }
  .card--back .wordmark__mark { width: 26px; height: 26px; }

  .card__divider {
    position: absolute;
    left: 384px;
    top: 48px;
    width: 3px;
    height: 270px;
    background: linear-gradient(180deg, rgba(0,0,0,0) 0%, #1a1a1a 25%, #4a4a4a 70%, rgba(0,0,0,0) 100%);
  }

  .holder {
    position: absolute;
    left: 418px;
    top: 70px;
  }
  .holder__name {
    font-size: 19px;
    font-weight: 800;
    color: var(--ink);
    letter-spacing: 0.02em;
    text-transform: uppercase;
  }
  .holder__role {
    font-size: 14px;
    font-weight: 700;
    color: var(--red);
    text-transform: uppercase;
    margin-top: 3px;
  }

  .contact {
    position: absolute;
    left: 418px;
    top: 196px;
    list-style: none;
  }
  .contact__item {
    display: flex;
    align-items: center;
    gap: 10px;
    font-size: 13px;
    font-weight: 500;
    color: var(--muted);
    margin-bottom: 10px;
  }
  .contact__icon {
    width: 14px;
    height: 14px;
    flex: none;
    fill: var(--red);
    stroke: var(--red);
  }
</style>
</head>
<body>

  <section class="card card--front">
    <div class="wordmark">
      <span class="wordmark__mark"></span>
      <span class="wordmark__name">Norvane Software</span>
    </div>
    <svg class="card__band" viewBox="0 0 660 40" aria-hidden="true">
      <path class="band__black" d="M470 40 C484 40 486 12 512 12 H660 V40 Z"/>
      <path class="band__red" d="M0 28 H462 C472 28 476 34 478 40 H0 Z"/>
    </svg>
  </section>

  <section class="card card--back">
    <div class="wordmark">
      <span class="wordmark__mark"></span>
      <span class="wordmark__name">Norvane Software</span>
    </div>

    <div class="card__divider"></div>

    <div class="holder">
      <p class="holder__name">Daniel Moreau</p>
      <p class="holder__role">Managing Director</p>
    </div>

    <ul class="contact">
      <li class="contact__item">
        <svg class="contact__icon" viewBox="0 0 16 16" aria-hidden="true" stroke-width="0">
          <path d="M2 6 C2 3 5 2 8 2 C11 2 14 3 14 6 L11 7 L10 5 H6 L5 7 Z"/>
          <rect x="3" y="8" width="10" height="6" rx="1"/>
        </svg>
        <span>0400 555 019</span>
      </li>
      <li class="contact__item">
        <svg class="contact__icon" viewBox="0 0 16 16" aria-hidden="true" stroke-width="0">
          <rect x="1" y="3" width="14" height="10" rx="1"/>
          <path d="M1.5 4 L8 9 L14.5 4" fill="none" stroke="#ffffff" stroke-width="1.4"/>
        </svg>
        <span>hello@norvanesoftware.com</span>
      </li>
      <li class="contact__item">
        <svg class="contact__icon" viewBox="0 0 16 16" aria-hidden="true" fill="none" stroke-width="1.8">
          <rect x="2" y="7" width="7" height="4" rx="2" transform="rotate(-45 5.5 9)"/>
          <rect x="7" y="5" width="7" height="4" rx="2" transform="rotate(-45 10.5 7)"/>
        </svg>
        <span>www.norvanesoftware.com</span>
      </li>
    </ul>

    <svg class="card__band" viewBox="0 0 660 40" aria-hidden="true">
      <path class="band__black" d="M470 40 C484 40 486 12 512 12 H660 V40 Z"/>
      <path class="band__red" d="M0 28 H462 C472 28 476 34 478 40 H0 Z"/>
    </svg>
  </section>

</body>
</html>
```